Coastline Premier Retreats Business Card Design

Design a business card for Coastline Premier Retreats. Look at the website for colors and reference. Card should have logo, name, title, office number, mobile number, email, URL and a tagline like, "Luxury Hotel & Resort Email Marketing" (This might change).

https://www.coastlinepremierretreats.example

The rest I will leave up to your imagination.

Contact Information for Business Card

Logo, name, title, office number, mobile number, email, URL and a tagline like, "Luxury Hotel & Resort Email Marketing" (This might change).

```html
<!DOCTYPE html>
<html lang="en">
<head>
<meta charset="utf-8">
<title>Coastline Premier Retreats – Business Card</title>
<link href="https://fonts.googleapis.com/css2?family=Open+Sans:wght@400;600;700&display=swap" rel="stylesheet">
<style>
  :root {
    --stage: #222223;
    --card-dark: #1f1f21;
    --orange: #f47421;
    --orange-deep: #e0621a;
    --white: #ffffff;
    --shadow: rgba(0, 0, 0, 0.55);
  }
  * { box-sizing: border-box; margin: 0; padding: 0; }
  html, body {
    width: 1200px;
    height: 780px;
    overflow: hidden;
    background: var(--stage);
    font-family: "Open Sans", Arial, sans-serif;
  }
  .stage {
    position: relative;
    width: 1200px;
    height: 780px;
  }
  .card {
    position: absolute;
    top: 110px;
    width: 320px;
    height: 560px;
    border-radius: 22px;
    box-shadow: 0 14px 30px var(--shadow);
    overflow: hidden;
  }

  /* Back side: orange with large set name */
  .card-back {
    left: 230px;
    background: var(--orange);
  }
  .back-name {
    position: absolute;
    left: 50%;
    top: 50%;
    width: 460px;
    transform: translate(-50%, -50%) rotate(-90deg);
    text-align: center;
    color: var(--orange-deep);
    font-weight: 700;
    font-size: 40px;
    line-height: 1.1;
    letter-spacing: 2px;
    text-transform: uppercase;
  }

  /* Front side: dark with details */
  .card-front {
    left: 650px;
    background: var(--card-dark);
    border-right: 3px solid var(--orange);
    border-bottom: 3px solid var(--orange);
    color: var(--white);
  }
  .brand {
    position: absolute;
    top: 44px;
    left: 32px;
    right: 32px;
    display: flex;
    align-items: center;
    gap: 10px;
  }
  .brand-mark {
    flex: none;
    width: 14px;
    height: 14px;
    background: var(--orange);
  }
  .brand-name {
    font-weight: 700;
    font-size: 19px;
    line-height: 1.15;
    letter-spacing: 0.5px;
    text-transform: uppercase;
    color: var(--white);
  }
  .profile {
    position: absolute;
    left: 32px;
    right: 24px;
    top: 300px;
  }
  .person-name {
    font-size: 30px;
    font-weight: 700;
    line-height: 1.1;
  }
  .person-name .first { color: var(--orange); }
  .person-name .last { color: var(--white); }
  .person-title {
    margin-top: 4px;
    font-size: 14px;
    font-weight: 600;
  }
  .tagline {
    margin-top: 14px;
    font-size: 13px;
    line-height: 1.35;
    color: var(--orange);
  }
  .contact-list {
    list-style: none;
    margin-top: 16px;
  }
  .contact-list li {
    display: flex;
    align-items: center;
    gap: 9px;
    font-size: 11.5px;
    line-height: 1.9;
    white-space: nowrap;
  }
  .contact-list svg {
    flex: none;
    width: 12px;
    height: 12px;
    fill: none;
    stroke: var(--orange);
    stroke-width: 1.6;
    stroke-linecap: round;
    stroke-linejoin: round;
  }
</style>
</head>
<body>
<main class="stage">

  <section class="card card-back" aria-label="Business card back">
    <p class="back-name">Coastline Premier Retreats</p>
  </section>

  <section class="card card-front" aria-label="Business card front">
    <header class="brand">
      <span class="brand-mark"></span>
      <span class="brand-name">Coastline Premier Retreats</span>
    </header>

    <div class="profile">
      <h1 class="person-name"><span class="first">Marina</span> <span class="last">Holloway</span></h1>
      <p class="person-title">Co-Founder</p>
      <p class="tagline">Luxury Hotel &amp;<br>Resort Email Marketing</p>

      <ul class="contact-list">
        <li>
          <svg viewBox="0 0 12 12" aria-hidden="true"><path d="M2 1.5 L4 1.5 L5 4 L3.8 5 Q5 7.5 7 8.2 L8 7 L10.5 8 L10.5 10 Q6 11 3 8 Q1 5.5 2 1.5 Z"/></svg>
          (555) 014-2758
        </li>
        <li>
          <svg viewBox="0 0 12 12" aria-hidden="true"><rect x="3" y="1" width="6" height="10" rx="1"/><path d="M5.3 9.3 H6.7"/></svg>
          (555) 019-7777
        </li>
        <li>
          <svg viewBox="0 0 12 12" aria-hidden="true"><circle cx="6" cy="6" r="4.7"/><path d="M1.3 6 H10.7 M6 1.3 Q3.5 6 6 10.7 M6 1.3 Q8.5 6 6 10.7"/></svg>
          www.coastlinepremierretreats.example
        </li>
        <li>
          <svg viewBox="0 0 12 12" aria-hidden="true"><rect x="1" y="2.5" width="10" height="7" rx="0.8"/><path d="M1.3 3 L6 6.5 L10.7 3"/></svg>
          info@coastlinepremierretreats.example
        </li>
      </ul>
    </div>
  </section>

</main>
</body>
</html>
```